BRIARWELL TAVERN FRIDAY MAY 3

Flyer design for bar/nightclub event. Trying to keep a general theme with their flyers (see below) but would like to add some neon or some pop to it.

TEXT:

Briarwell Bar & Tavern Presents

LANTERNTIDE NIGHTS
GRAND OPENING EVENT

PURE HOUSE MUSIC W/

MORVEX
TOMAS HALVERO
BENNAR & ACE DRIFTWAY

21+
9PM-130AM
518 M AVENUE DAVIS CA

Target Market(s)

House/dance music crowd.

Industry/Entity Type

Night Club

Font styles to use
Sans Serif

Colors
9bcb3c
fbee3d
ffffff

Requirements
Must have
• Large DJ names
Nice to have
• General theme of the attached flyers. Neon colors that stick with the theme. Anything else that looks cool will be considered

```html
<!DOCTYPE html>
<html lang="en">
<head>
<meta charset="utf-8">
<title>Lanterntide Nights – Grand Opening</title>
<link rel="stylesheet" href="https://fonts.googleapis.com/css2?family=Montserrat:wght@300;400;500;700;800&display=swap">
<style>
  :root {
    --lime: #9bcb3c;
    --lime-light: #d4ea4a;
    --yellow: #fbee3d;
    --white: #ffffff;
    --brown: #3a2e22;
    --olive: #7d8c3a;
    --olive-dark: #66742f;
    --gold: #e8a92a;
    --cream: #f3ead8;
    --text-dark: #3a2e22;
    --neon-glow: 0 0 6px rgba(251,238,61,0.9), 0 0 16px rgba(251,238,61,0.6), 0 0 30px rgba(212,234,74,0.45);
  }
  * { margin: 0; padding: 0; box-sizing: border-box; }
  html, body { width: 849px; height: 1200px; overflow: hidden; background: #fff; }
  .flyer {
    position: relative;
    width: 849px;
    height: 1200px;
    overflow: hidden;
    font-family: "Montserrat", sans-serif;
    color: var(--text-dark);
    background: radial-gradient(ellipse at 0% 0%, var(--lime-light) 0%, var(--lime) 50%, #8fc23a 100%);
  }

  .tree-art {
    position: absolute;
    top: -10px;
    width: 230px;
    height: 190px;
    border-radius: 50%;
    background: radial-gradient(ellipse at 50% 45%, rgba(108,122,48,0.6) 0%, rgba(108,122,48,0.3) 55%, rgba(108,122,48,0) 72%);
  }
  .tree-art--left { left: -20px; }
  .tree-art--right { right: -20px; }

  .venue-mark {
    position: absolute;
    left: 251px;
    top: 37px;
    width: 347px;
    height: 101px;
    background: var(--brown);
    border: 3px solid var(--gold);
    display: flex;
    align-items: center;
    padding: 0 16px 0 12px;
    gap: 14px;
    box-shadow: 0 0 14px rgba(251,238,61,0.55);
  }
  .venue-mark__square { width: 72px; height: 72px; background: #2f4a3c; flex: none; }
  .venue-mark__name { flex: 1; text-align: center; color: var(--cream); font-weight: 700; line-height: 1; }
  .venue-mark__title { display: block; font-size: 30px; letter-spacing: 0.5px; }
  .venue-mark__sub { display: block; font-size: 13px; margin-top: 6px; letter-spacing: 1px; }
  .venue-mark__presents { display: block; font-size: 9px; margin-top: 5px; letter-spacing: 2px; color: var(--yellow); }

  .title-band {
    position: absolute;
    left: 0;
    top: 186px;
    width: 849px;
    height: 156px;
    background: var(--brown);
  }
  .series-name {
    position: absolute;
    left: 40px;
    top: 196px;
    font-size: 52px;
    font-weight: 400;
    line-height: 62px;
    letter-spacing: 1px;
    color: var(--yellow);
    text-shadow: var(--neon-glow);
  }
  .opening-bar {
    position: absolute;
    left: 30px;
    top: 267px;
    width: 768px;
    height: 63px;
    display: flex;
    align-items: center;
    padding-left: 14px;
    font-size: 50px;
    letter-spacing: 0.5px;
    white-space: nowrap;
    color: var(--text-dark);
    background: linear-gradient(90deg, var(--yellow) 0%, var(--lime-light) 55%, var(--lime) 100%);
    box-shadow: 0 0 10px rgba(251,238,61,0.8), 0 0 24px rgba(251,238,61,0.45);
  }
  .opening-bar strong { font-weight: 700; margin-right: 14px; }
  .opening-bar span { font-weight: 400; }

  .music-line {
    position: absolute;
    left: 42px;
    top: 360px;
    font-size: 44px;
    font-weight: 400;
    line-height: 56px;
    letter-spacing: 0.5px;
  }

  .lineup {
    position: absolute;
    left: 0;
    top: 470px;
    width: 849px;
    list-style: none;
    text-align: center;
  }
  .lineup__headliner {
    font-size: 68px;
    font-weight: 800;
    line-height: 84px;
    letter-spacing: 3px;
    color: var(--white);
    text-shadow: 0 0 2px var(--brown), 0 0 10px rgba(251,238,61,0.95), 0 0 24px rgba(251,238,61,0.6);
    -webkit-text-stroke: 2px var(--brown);
  }
  .lineup__act {
    font-size: 54px;
    font-weight: 500;
    line-height: 72px;
    letter-spacing: 1px;
  }
  .lineup__act--small { font-size: 48px; }

  .forest-art {
    position: absolute;
    left: 0;
    bottom: 0;
    width: 849px;
    height: 250px;
    background: linear-gradient(180deg, rgba(125,140,58,0) 0%, var(--olive) 28%, var(--olive-dark) 100%);
  }
  .forest-art--rise {
    left: auto;
    right: -120px;
    bottom: 120px;
    width: 420px;
    height: 360px;
    border-radius: 50% 50% 0 0;
    background: radial-gradient(ellipse at 60% 100%, var(--olive) 0%, rgba(125,140,58,0.7) 45%, rgba(125,140,58,0) 72%);
  }

  .details {
    position: absolute;
    left: 14px;
    top: 802px;
    width: 640px;
    height: 192px;
    list-style: none;
    background: var(--brown);
    padding: 7px 9px;
    display: flex;
    flex-direction: column;
    gap: 5px;
    box-shadow: 0 0 14px rgba(251,238,61,0.6);
  }
  .details__row {
    flex: 1;
    display: flex;
    align-items: center;
    padding-left: 22px;
    font-size: 42px;
    font-weight: 700;
    letter-spacing: 0.5px;
    color: var(--text-dark);
    background: linear-gradient(90deg, var(--yellow) 0%, var(--lime-light) 45%, var(--lime) 100%);
  }
</style>
</head>
<body>
<main class="flyer">
  <div class="tree-art tree-art--left" role="img" aria-label="Leafy tree branches"></div>
  <div class="tree-art tree-art--right" role="img" aria-label="Leafy tree branches"></div>

  <div class="forest-art forest-art--rise" role="img" aria-label="Pine forest silhouette"></div>
  <div class="forest-art" role="img" aria-label="Pine forest silhouette"></div>

  <header class="venue-mark">
    <span class="venue-mark__square"></span>
    <p class="venue-mark__name">
      <span class="venue-mark__title">BRIARWELL</span>
      <span class="venue-mark__sub">BAR &amp; TAVERN</span>
      <span class="venue-mark__presents">PRESENTS</span>
    </p>
  </header>

  <div class="title-band"></div>
  <h1 class="series-name">LANTERNTIDE NIGHTS</h1>
  <h2 class="opening-bar"><strong>GRAND OPENING</strong><span>EVENT</span></h2>

  <p class="music-line">PURE HOUSE MUSIC W/</p>

  <ul class="lineup">
    <li class="lineup__headliner">MORVEX</li>
    <li class="lineup__act">TOMAS HALVERO</li>
    <li class="lineup__act lineup__act--small">BENNAR &amp; ACE DRIFTWAY</li>
  </ul>

  <ul class="details">
    <li class="details__row">21+</li>
    <li class="details__row">9PM-130AM</li>
    <li class="details__row">518 M AVENUE DAVIS CA</li>
  </ul>
</main>
</body>
</html>
```